Acupuncture business needs business card design

I need a business card for an acupuncture clinic called "Harbourlight Wellness"
It will need the following details:
My name: Marcus Pelling
Acupuncturist
Member TVBH
KWF Treatment Provider
Ph numbers: 581 2734 027 418 5620
Email: marcus@hbwel.example.nz
On the back it will need a table with 2 columns for appointments, one column for time and one for date.

Industry/Entity Type

Clinic

Contact Information for Business Card

Marcus Pelling
Acupuncturist
Member TVBH
KWF Treatment Provider
Email: marcus@hbwel.example.nz

Requirements
Must have
• Marcus Pelling
• Acupuncturist
• Member TVBH
• KWF Treatment Provider
• Ph numbers: 581 2734 027 418 5620
• Email: marcus@hbwel.example.nz
• On the back it will need a table with 2 columns for appointments, one column for time and one for date.

```html
<!DOCTYPE html>
<html lang="en">
<head>
<meta charset="utf-8">
<title>Harbourlight Wellness – Business Card</title>
<link rel="stylesheet" href="https://fonts.googleapis.com/css2?family=Open+Sans:wght@400;600;700&display=swap">
<style>
  :root {
    --blue: #0aabe0;
    --blue-deep: #0b8fc4;
    --ink: #2b3f4c;
    --paper: #ffffff;
    --stage: #e9ecef;
    --bar: rgba(255, 255, 255, 0.72);
    --faint: rgba(255, 255, 255, 0.14);
  }
  * { box-sizing: border-box; margin: 0; padding: 0; }
  html, body {
    width: 1200px; height: 948px; overflow: hidden;
    background: var(--stage);
    font-family: "Open Sans", Arial, sans-serif;
  }
  .sheet {
    width: 1200px; height: 948px;
    display: flex; align-items: center; justify-content: center; gap: 40px;
  }
  .card {
    width: 540px; height: 310px; position: relative; overflow: hidden;
    border-radius: 4px;
    box-shadow: 0 10px 30px rgba(0, 0, 0, 0.18);
  }

  /* Front */
  .card-front { background: var(--paper); }
  .brand {
    position: absolute; left: 96px; top: 38px;
    display: flex; align-items: center; gap: 12px;
  }
  .brand-dot {
    width: 34px; height: 34px; border-radius: 50%;
    background: var(--blue);
  }
  .brand-name {
    font-weight: 700; font-size: 28px; color: var(--blue-deep);
    letter-spacing: -0.3px; line-height: 1;
  }
  .brand-tagline {
    position: absolute; left: 142px; top: 74px;
    font-size: 8.5px; letter-spacing: 3.6px; color: var(--blue-deep);
    text-transform: uppercase;
  }
  .practitioner { position: absolute; left: 60px; top: 116px; }
  .practitioner-line { font-size: 12px; color: var(--ink); }
  .practitioner-name { font-weight: 700; font-size: 14px; }
  .practitioner-role { font-size: 11.5px; color: var(--blue-deep); margin-top: 3px; }
  .rule {
    position: absolute; left: 0; right: 0; top: 196px;
    height: 3px; background: var(--blue-deep);
  }
  .contact-band {
    position: absolute; left: 0; right: 0; bottom: 0; height: 106px;
    background: var(--blue);
    display: flex; align-items: center; color: var(--paper);
    font-size: 12px; line-height: 1.65;
  }
  .address { width: 240px; padding-left: 34px; }
  .divider { width: 1px; height: 58px; background: rgba(255,255,255,0.7); }
  .contacts { padding-left: 22px; }
  .contact-row { display: flex; align-items: center; gap: 8px; }
  .contact-row svg { width: 13px; height: 13px; flex: none; }

  /* Back */
  .card-back { background: var(--blue); color: var(--paper); }
  .back-circle {
    position: absolute; left: 150px; top: 40px;
    width: 240px; height: 240px; border-radius: 50%;
    background: var(--faint);
  }
  .appointments { position: absolute; left: 70px; top: 52px; width: 400px; }
  .appointments-head {
    display: grid; grid-template-columns: 1fr 1fr; column-gap: 18px;
    font-size: 15px; margin-bottom: 10px;
  }
  .appointments-row {
    display: grid; grid-template-columns: 1fr 1fr; column-gap: 18px;
    margin-bottom: 12px;
  }
  .slot { height: 22px; background: var(--bar); }
  .web-address {
    position: absolute; left: 0; right: 0; bottom: 30px; text-align: center;
    font-size: 17px; letter-spacing: 4px;
  }
</style>
</head>
<body>
<main class="sheet">
  <section class="card card-front" aria-label="Business card front">
    <div class="brand">
      <span class="brand-dot"></span>
      <span class="brand-name">Harbourlight Wellness</span>
    </div>
    <div class="brand-tagline">Acupuncture Physiotherapy</div>

    <div class="practitioner">
      <p class="practitioner-line"><span class="practitioner-name">Marcus Pelling,</span> Acupuncturist Member TVBH</p>
      <p class="practitioner-role">KWF Treatment Provider</p>
    </div>

    <div class="rule"></div>

    <div class="contact-band">
      <div class="address">
        <p>Street Name, City Name</p>
        <p>Zipcode-01234</p>
      </div>
      <div class="divider"></div>
      <div class="contacts">
        <p class="contact-row">
          <svg viewBox="0 0 16 16" aria-hidden="true"><circle cx="8" cy="8" r="7" fill="none" stroke="#fff" stroke-width="1.4"/><path d="M5.6 4.6l1.2 1.6-.7.9c.5 1 1.3 1.8 2.3 2.3l.9-.7 1.6 1.2-.7 1.3c-2.6-.4-4.6-2.4-5-5z" fill="#fff"/></svg>
          581 2734 / 027 418 5620
        </p>
        <p class="contact-row">
          <svg viewBox="0 0 16 16" aria-hidden="true"><circle cx="8" cy="8" r="7.5" fill="#fff"/><rect x="4" y="5" width="8" height="6" fill="none" stroke="#0aabe0" stroke-width="1.2"/><path d="M4 5l4 3.2L12 5" fill="none" stroke="#0aabe0" stroke-width="1.2"/></svg>
          marcus@hbwel.example.nz
        </p>
      </div>
    </div>
  </section>

  <section class="card card-back" aria-label="Business card back">
    <div class="back-circle"></div>
    <div class="appointments">
      <div class="appointments-head"><span>Date</span><span>Time</span></div>
      <div class="appointments-row"><span class="slot"></span><span class="slot"></span></div>
      <div class="appointments-row"><span class="slot"></span><span class="slot"></span></div>
      <div class="appointments-row"><span class="slot"></span><span class="slot"></span></div>
      <div class="appointments-row"><span class="slot"></span><span class="slot"></span></div>
    </div>
    <p class="web-address">www.hbwel.example.nz</p>
  </section>
</main>
</body>
</html>
```